A4 Single Sided Brochure Folder Design Technical Company

We are a technical company based in the UK, working worldwide for Power Distribution companies.

We have technical literature and need a folder to present these in. The design should be very simple and clean using our logo and "Reliable Network Engineering"

Our website kestrome.com gives and idea of the business but don't follow the look of the website as we will be redoing shortly.

• Logo and Strap Line
• Clean, easy to print and timeless
• Shouldn't be fashionable, we certainly aren't

```html
<!DOCTYPE html>
<html lang="en">
<head>
<meta charset="utf-8">
<title>Kestrome Presentation Folder</title>
<link rel="stylesheet" href="https://fonts.googleapis.com/css2?family=Quicksand:wght@400;500&display=swap">
<style>
  :root {
    --backdrop: #d9d9d9;
    --paper: #ffffff;
    --band: #b82e8c;
    --band-deep: #a52a7f;
    --logo-ink: #ffffff;
    --strap-ink: #6d3a5e;
    --url-ink: #7a2a62;
    --fold-line: #e4e4e4;
  }
  * { margin: 0; padding: 0; box-sizing: border-box; }
  html, body {
    width: 1200px;
    height: 750px;
    overflow: hidden;
  }
  body {
    background: radial-gradient(ellipse at 50% 45%, #f1f1f1 0%, var(--backdrop) 75%);
    font-family: "Quicksand", sans-serif;
    display: flex;
    align-items: center;
    justify-content: center;
  }
  .folder-spread {
    display: flex;
    width: 792px;
    height: 560px;
    box-shadow: 0 14px 30px rgba(0, 0, 0, 0.18);
  }
  .panel {
    position: relative;
    width: 396px;
    height: 560px;
    background: var(--paper);
  }
  .panel--back {
    border-right: 1px solid var(--fold-line);
  }
  .band {
    position: absolute;
    left: 0;
    right: 0;
    top: 206px;
    height: 92px;
    background: var(--band);
  }
  .panel--back .band {
    background: var(--band-deep);
  }
  .band__url {
    position: absolute;
    left: 0;
    right: 0;
    top: 40px;
    text-align: center;
    font-size: 9px;
    letter-spacing: 0.04em;
    color: var(--url-ink);
  }
  .brand {
    position: absolute;
    left: 0;
    right: 0;
    top: 10px;
    text-align: center;
  }
  .brand__name {
    display: block;
    font-size: 42px;
    font-weight: 400;
    line-height: 1;
    letter-spacing: 0.02em;
    color: var(--logo-ink);
  }
  .brand__strap {
    display: block;
    margin-top: 14px;
    font-size: 14px;
    font-weight: 500;
    line-height: 1.2;
    letter-spacing: 0.02em;
    color: var(--strap-ink);
  }
</style>
</head>
<body>
  <main class="folder-spread">
    <section class="panel panel--back" aria-label="Back cover">
      <div class="band">
        <p class="band__url">www.kestrome.com</p>
      </div>
    </section>
    <section class="panel panel--front" aria-label="Front cover">
      <div class="band">
        <div class="brand">
          <span class="brand__name">Kestrome</span>
          <span class="brand__strap">Reliable Network Engineering</span>
        </div>
      </div>
    </section>
  </main>
</body>
</html>
```